Makers' Hollow - Landing page for small and large screen

Makers’ Hollow gives you the space you need to take your side project from idea to reality.

With three days of focused work, it’s a place for you iron out the details of your business idea away from the distractions of the city.

The full copy and structure is here:
https://www.makershollow.co.uk/landing

What it needs, a touch of colour.

Target Market(s)

25-35 working in digital industry, software developer, a UI or UX designer

Number of Pages Required

1 page

Font styles to use
Sans Serif

Colors
0292cd
33b8a4
86cfc6
fdf9cf
ec1f27

Requirements
Should not have
• gradients or too much images

```html
<!DOCTYPE html>
<html lang="en">
<head>
<meta charset="utf-8">
<title>Makers' Hollow – Landing</title>
<link rel="stylesheet" href="https://fonts.googleapis.com/css2?family=Roboto:wght@400;500;700;900&family=Open+Sans:wght@400;600&display=swap">
<style>
:root{
  --blue:#0292cd;
  --deep-blue:#1568a8;
  --teal:#33b8a4;
  --mint:#86cfc6;
  --cream:#fdf9cf;
  --red:#ec1f27;
  --ink:#222222;
  --body:#444444;
  --grey-band:#eeeeef;
  --footer:#141414;
  --white:#ffffff;
}
*{margin:0;padding:0;box-sizing:border-box}
html,body{width:1200px;height:4167px;overflow:hidden;background:var(--white)}
body{font-family:'Open Sans',sans-serif;color:var(--body);position:relative}
.abs{position:absolute}
h1,h2,h3{font-family:'Roboto',sans-serif}

/* hero */
.hero{left:0;top:0;width:1200px;height:625px;background:linear-gradient(160deg,#6b6a68 0%,#3e3c3a 45%,#5a4a3e 75%,#2d2b29 100%)}
.brand{left:143px;top:50px;color:var(--white);font-family:'Roboto',sans-serif;font-weight:700;font-size:41px;letter-spacing:-.3px}
.brand-tag{left:145px;top:104px;color:var(--white);font-size:18px}
.phone{left:775px;top:48px;display:flex;align-items:center;gap:14px;color:var(--white);font-family:'Roboto',sans-serif;font-weight:500;font-size:21px}
.phone-dot{width:36px;height:36px;border-radius:50%;background:var(--blue);display:flex;align-items:center;justify-content:center}
.nav{left:528px;top:105px;display:flex;gap:32px;font-family:'Roboto',sans-serif;font-weight:500;font-size:17px;color:var(--white)}
.hero-title{left:0;top:316px;width:1200px;text-align:center;color:var(--white);font-weight:700;font-size:42px;letter-spacing:0}
.btn-ghost{left:497px;top:404px;width:206px;height:46px;border:2px solid var(--white);border-radius:23px;color:var(--white);font-family:'Roboto',sans-serif;font-weight:500;font-size:18px;display:flex;align-items:center;justify-content:center}
.notch{left:570px;top:593px;width:60px;height:64px}

/* intro */
.intro-frame{left:122px;top:732px;width:400px;height:420px;border-left:5px solid var(--blue);border-bottom:5px solid var(--blue)}
.intro-photo{left:132px;top:735px;width:398px;height:420px;background:linear-gradient(135deg,#c9c6c1,#8f8a86 50%,#5c5a5c)}
.intro-heading{left:570px;top:733px;width:520px;color:var(--ink);font-weight:700;font-size:25px;line-height:40px}
.rule{height:3px;width:62px;background:var(--blue)}
.intro-copy{left:570px;top:893px;width:520px;font-size:14.5px;line-height:25px}
.intro-copy p{margin-bottom:16px}

.lead{left:0;top:1248px;width:1200px;text-align:center;color:var(--ink);font-weight:700;font-size:25px;line-height:44px}
.lead-copy{left:230px;top:1435px;width:740px;text-align:center;font-size:14.5px;line-height:27px}
.lead-copy p{margin-bottom:16px}

/* features */
.features{left:0;top:1722px;width:1200px;height:700px;background:var(--grey-band)}
.feat{font-size:17px;line-height:26px;color:var(--ink);width:300px}
.feat.left{text-align:right}
.hub{left:421px;top:1805px;width:370px;height:370px}
.hub-text{left:421px;top:1958px;width:370px;text-align:center;font-family:'Roboto',sans-serif;font-weight:400;font-size:29px;line-height:38px;color:var(--ink)}
.hub-text b{font-weight:700}

/* stay */
.stay{left:0;top:2290px;width:1200px;height:490px}
.stay-title{left:0;top:2460px;width:1200px;text-align:center;color:var(--white);font-weight:700;font-size:38px}
.stay-copy{left:190px;top:2575px;width:820px;text-align:center;color:var(--white);font-size:17px;line-height:31px}

/* organisers */
.org-title{left:0;top:2868px;width:1200px;text-align:center;font-family:'Roboto',sans-serif;font-weight:400;font-size:33px;color:var(--ink);letter-spacing:.5px}
.org-title b{font-weight:900}
.card{width:406px;height:292px;background:var(--white);border-radius:6px;box-shadow:0 2px 12px rgba(0,0,0,.18);padding:34px 30px}
.card p{font-size:13px;line-height:24px;color:var(--body)}
.card .who{position:absolute;bottom:28px;font-size:17px;line-height:25px;color:var(--blue)}
.quote{position:absolute;bottom:18px;font-family:'Roboto',sans-serif;font-size:110px;line-height:70px;height:50px;color:#8a8a8a;font-weight:700}
.avatar{width:114px;height:114px;border-radius:50%;background:radial-gradient(circle at 50% 40%,#8e8e8e,#2b2b2b 70%)}

/* feedback */
.feedback{left:0;top:3422px;width:1200px;height:470px;background:#f3f3f3}
.feedback-photo{left:0;top:3422px;width:560px;height:470px;background:linear-gradient(120deg,#e3e3e3,#bdbdbd 45%,#f0f0f0)}
.fb-title{left:564px;top:3540px;font-weight:700;font-size:36px;color:var(--ink)}
.fb-copy{left:564px;top:3637px;width:470px;font-size:15px;line-height:28px}
.btn-line{left:564px;top:3718px;width:272px;height:42px;border:2px solid var(--blue);border-radius:21px;color:var(--blue);font-family:'Roboto',sans-serif;font-weight:700;font-size:15px;display:flex;align-items:center;justify-content:center;letter-spacing:.5px}

/* footer */
.footer{left:0;top:3860px;width:1200px;height:307px}
.foot-links{left:0;top:3972px;width:1200px;text-align:center;color:var(--white);font-size:17px}
.foot-links span{margin:0 12px}
.copyright{left:0;top:4016px;width:1200px;text-align:center;color:var(--white);font-size:17px}
.socials{left:530px;top:4073px;display:flex;gap:8px}
.socials i{width:28px;height:28px;border:2px solid var(--white);border-radius:50%;display:block}
</style>
</head>
<body>

<header class="abs hero" role="img" aria-label="Photo of a person working at a laptop on a wooden desk, seen from above"></header>
<div class="abs brand">Makers' Hollow</div>
<div class="abs brand-tag">create. connect. collaborate</div>
<div class="abs phone"><span class="phone-dot"><svg width="18" height="18" viewBox="0 0 24 24"><path fill="#fff" d="M6.6 10.8a15 15 0 0 0 6.6 6.6l2.2-2.2c.3-.3.7-.4 1-.2 1.1.4 2.3.6 3.6.6.6 0 1 .4 1 1V20c0 .6-.4 1-1 1A17 17 0 0 1 3 4c0-.6.4-1 1-1h3.5c.6 0 1 .4 1 1 0 1.3.2 2.5.6 3.6.1.3 0 .7-.2 1z"/></svg></span>Call Us : (888) 0147 2290</div>
<nav class="abs nav"><span>HOME</span><span>ABOUT US</span><span>OUR SERVICES</span><span>BLOG</span><span>CONTACT US</span></nav>
<h1 class="abs hero-title">CREATE. CONNECT. COLLABORATE</h1>
<div class="abs btn-ghost">GET MORE INFO</div>
<svg class="abs notch" viewBox="0 0 60 64"><path d="M0 32 A30 30 0 0 1 60 32 L60 64 L0 64Z" fill="#fff"/><path d="M30 20v22M22 35l8 8 8-8" stroke="#0292cd" stroke-width="2.5" fill="none"/></svg>

<section>
  <div class="abs intro-frame"></div>
  <div class="abs intro-photo" role="img" aria-label="Photo of a woman with glasses working on a laptop"></div>
  <h2 class="abs intro-heading">MAKERS’ HOLLOW GIVES YOU<br>THE SPACE YOU NEED TO TAKE YOUR<br>SIDE PROJECT FROM IDEA TO REALITY.</h2>
  <div class="abs rule" style="left:570px;top:866px"></div>
  <div class="abs intro-copy">
    <p>Calling all creatives! Whether you’re a software developer, a UI or UX designer, a product creator or an artworker, you’ll know only too well that great work rarely materialises when you’re in the wrong environment.</p>
    <p>Phones buzzing. Emails pinging. Chattervox calls incoming...distractions are everywhere – and they do nothing for your motivation.</p>
    <p>So, if you have a seed of a business idea and need to reclaim some focus, Makers’ Hollow is for you. Or maybe you’ve created a product, sought a patent and you’re ready – and raring – to go.</p>
  </div>
</section>

<section>
  <h2 class="abs lead">WITH THREE DAYS OF FOCUSED WORK, IT’S A PLACE FOR YOU<br>IRON OUT THE DETAILS OF YOUR BUSINESS IDEA AWAY FROM<br>THE DISTRACTIONS OF THE CITY.</h2>
  <div class="abs rule" style="left:569px;top:1406px"></div>
  <div class="abs lead-copy">
    <p>Whatever stage your side hustle’s at, we’re here to help it thrive. Our warm and friendly Retreat is just that: a place to create, connect and collaborate with likeminded folks. Oh, and there’s yoga, meditation, healthy meals and snacks, and all the feedback you need to power on through.</p>
    <p>And while you’re busy getting your side project off the ground, we’ll rustle up three healthy meals each day so that you don’t have to worry about cooking. We’ll even make sure you have a steady supply of healthy, low-sugar snacks to help fuel all those bright ideas.</p>
  </div>
</section>

<section>
  <div class="abs features"></div>
  <svg class="abs hub" viewBox="0 0 370 370">
    <circle cx="185" cy="185" r="178" fill="#f7f7f7" stroke="#33b8a4" stroke-width="3"/>
    <circle cx="185" cy="185" r="156" fill="#e9e6e3" opacity=".6"/>
  </svg>
  <div class="abs hub-text">JOIN THE RETREAT<br><b>AND ENJOY</b></div>

  <svg class="abs" style="left:0;top:1722px" width="1200" height="600" viewBox="0 1722 1200 600">
    <g fill="#33b8a4">
      <circle cx="467" cy="1869" r="31"/><circle cx="409" cy="1972" r="31"/><circle cx="440" cy="2081" r="31"/>
      <circle cx="745" cy="1869" r="31"/><circle cx="798" cy="1972" r="31"/><circle cx="770" cy="2081" r="31"/>
      <circle cx="625" cy="2190" r="31"/>
    </g>
    <g stroke="#fff" stroke-width="2.5" fill="none">
      <rect x="455" y="1858" width="24" height="22" rx="2"/><path d="M455 1865h24M461 1854v7M473 1854v7"/>
      <rect x="399" y="1959" width="20" height="26"/><path d="M404 1966h10M404 1972h10M404 1978h10"/>
      <path d="M430 2073h10v-6h8v8h-6v10h-12z"/>
      <path d="M733 1860h18a4 4 0 0 1 4 4v8a4 4 0 0 1-4 4h-10l-6 5v-5h-2a4 4 0 0 1-4-4v-8a4 4 0 0 1 4-4z" fill="#fff"/>
      <circle cx="798" cy="1962" r="4"/><path d="M786 1984c4-10 20-10 24 0M788 1972l10 4 10-4"/>
      <path d="M759 2072v18M765 2072v18M775 2072v18M781 2072c-5 4-5 10 0 18M763 2072v6"/>
      <circle cx="625" cy="2188" r="7"/><path d="M625 2173v5M625 2198v5M610 2188h5M635 2188h5M615 2178l3 3M632 2195l3 3M635 2178l-3 3M618 2195l-3 3"/>
    </g>
  </svg>

  <p class="abs feat left" style="left:117px;top:1838px">Three, full days of<br>distraction-free work</p>
  <p class="abs feat left" style="left:61px;top:1946px">A chance to hone your side<br>project away from the office</p>
  <p class="abs feat left" style="left:97px;top:2054px">The opportunity to collaborate<br>with likeminded creatives</p>
  <p class="abs feat" style="left:800px;top:1838px">Good, honest feedback and<br>insight from fellow attendees</p>
  <p class="abs feat" style="left:850px;top:1946px">Daily yoga and meditation<br>to help fuel your ideas</p>
  <p class="abs feat" style="left:825px;top:2054px">Three, nutritious and<br>delicious meals a day</p>
  <p class="abs feat" style="left:475px;top:2236px;text-align:center">Healthy, low-sugar snacks to<br>get you through the day</p>
</section>

<section>
  <svg class="abs stay" viewBox="0 0 1200 490" preserveAspectRatio="none">
    <path d="M0 40 Q600 -40 1200 40 L1200 490 L0 490Z" fill="#1568a8"/>
  </svg>
  <h2 class="abs stay-title">WHERE YOU’LL BE STAYING</h2>
  <div class="abs" style="left:569px;top:2541px;width:62px;height:3px;background:#fff"></div>
  <p class="abs stay-copy">A retreat wouldn’t be a retreat without a calm, peaceful and picturesque location. It’s the reason we’re working hard behind the scenes to find the ideal spot to host you. Of course, it’ll have Wi-Fi/4G internet – but it’ll also be somewhere that will allow for maximum creativity.</p>
</section>

<section>
  <h2 class="abs org-title"><b>MEET YOUR</b> RETREAT ORGANISERS</h2>
  <div class="abs card" style="left:158px;top:2972px">
    <p style="width:310px">A software engineer in London, Tobin knows only too well the challenges faced by creatives; it’s the reason he’s organised Makers’ Hollow, to give everyone the space and time to do their best work. Armed with his trusty camera, photographer Tobin is also a biohacker enthusiast and a thoroughly good egg.</p>
    <div class="who" style="left:24px">Tobin Marsh<br>Makers’ Hollow</div>
    <div class="quote" style="left:200px">”</div>
  </div>
  <div class="abs card" style="left:636px;top:2972px;text-align:right;padding-left:90px">
    <p>An internationally-certified yoga teacher, Elsa loves connecting with people and discovering how she can help them get the best out of their day – and their work. Giving attendees the time to enjoy some self-care in the form of a spot of gentle yoga, animal lover Elsa will help you unleash those ideas!</p>
    <div class="who" style="right:24px">Tobin Marsh<br>Makers’ Hollow</div>
    <div class="quote" style="left:160px">“</div>
  </div>
  <div class="abs avatar" style="left:461px;top:3180px" role="img" aria-label="Portrait photo of organiser Tobin"></div>
  <div class="abs avatar" style="left:604px;top:3180px" role="img" aria-label="Portrait photo of organiser Elsa"></div>
</section>

<section>
  <div class="abs feedback"></div>
  <div class="abs feedback-photo" role="img" aria-label="Photo of hands typing on a laptop beside a coffee cup and a small plant"></div>
  <h2 class="abs fb-title">WHAT DO YOU THINK?</h2>
  <div class="abs rule" style="left:564px;top:3610px"></div>
  <p class="abs fb-copy">Sound good? Keen to know more? Share some feedback via the button below and we can hone the Retreat to suit you.</p>
  <div class="abs btn-line">SHARE YOUR THOUGHTS...</div>
</section>

<footer>
  <svg class="abs footer" viewBox="0 0 1200 307">
    <path d="M0 30 H530 C560 30 565 0 600 0 C635 0 640 30 670 30 H1200 V307 H0Z" fill="#141414"/>
    <path d="M600 46V14M590 24l10-10 10 10" stroke="#fff" stroke-width="2.5" fill="none"/>
  </svg>
  <div class="abs foot-links"><span>Home</span>|<span>About Us</span>|<span>Services</span>|<span>Blog</span>|<span>Contact Us</span>|<span>FAQ</span></div>
  <div class="abs copyright">Copyright 2019 Makers’ Hollow. All rights reserved.</div>
  <div class="abs socials"><i></i><i></i><i></i><i></i></div>
</footer>

</body>
</html>
```